Homeowners Insurance Provider Website

We are selling homeowners insurance policy / tenants Policy/Flood Insurance in USA in few states and planning expand nationally.

Our target audience are two folds: Customers (Buy policies) and Insurance Agents who wants to work with us to sell our policies to customers. But website should focus 80% on customers and 20% on agents. So, more customer focused user experience. Please note that there is no direct buy option for customers. They always go through insurance agents.

Customer focused, educational that makes buyer journey easy. We don’t want to come off as trying sell something as there is no direct sales involved from website.

Target Market(s)

Homeowners in USA and Insurance agent who sells these insurance.

Industry/Entity Type

Insurance

Number of Pages Required

4 page

Font styles to use
Other font styles liked:
• Open to suggestions

Colors

Designer to choose colors to be used in the design.

Requirements
Must have
• Three most important things: Trustworthy, Authentic, Simple
• Please use colors form logo and grays
• We like: www.hollowmere.com
• https://www.quillfenbrook.com/
• We need Agent Look up tool on home page similar to what is shown on example sites.
• Design:
• Home Page - Open to Ideas
• Insurance (Products) Landing Page - Info similar to: https://www.quillfenbrook.com/insurance/
• Agents Page - https://www.quillfenbrook.com/agents/
• Claims Page - Information similar to: https://www.quillfenbrook.com/claims-center/
• Site Navigation:
• Home
• Insurance
• Claims
• Agents
• About Us
• Contact Us
Nice to have
• Elegant, minimal and clean design that reflects trust and authenticity.
Should not have
• Slider or rotating images - prefer flat design. Not over powering design.

```html
<!DOCTYPE html>
<html lang="en">
<head>
<meta charset="utf-8">
<title>Hearthline Insurance Co.</title>
<link href="https://fonts.googleapis.com/css2?family=Open+Sans:wght@400;600;700&family=Raleway:wght@400;500;600&display=swap" rel="stylesheet">
<style>
:root{
  --red:#d71f2c;
  --navy:#1e3a7b;
  --navy-deep:#14264f;
  --ink:#222;
  --gray:#555;
  --line:#c9c9c9;
  --light:#f4f4f4;
  --footer:#1d1d1d;
  --white:#fff;
}
*{box-sizing:border-box;margin:0;padding:0}
html,body{width:1200px;height:2903px;overflow:hidden}
body{position:relative;font-family:"Raleway",sans-serif;color:var(--ink);background:var(--white)}
.abs{position:absolute}
.head{font-family:"Open Sans",sans-serif}
.btn{position:absolute;display:flex;align-items:center;justify-content:center;font-family:"Open Sans",sans-serif;font-size:13px;font-weight:600;text-transform:uppercase;color:var(--white);letter-spacing:.3px;white-space:nowrap}
.btn-red{background:var(--red)}
.btn-navy{background:var(--navy)}
.btn-ghost{border:1px solid var(--white)}
.photo{position:absolute}

/* header */
.site-header{position:absolute;left:0;top:0;width:1200px;height:86px;background:rgba(255,255,255,.82);z-index:3}
.brand{position:absolute;left:150px;top:22px;height:40px;display:flex;align-items:center;gap:10px}
.brand-mark{width:36px;height:36px;background:var(--navy)}
.brand-name{font-family:"Open Sans",sans-serif;font-weight:700;font-size:16px;color:var(--navy);line-height:19px;white-space:nowrap}
.main-nav{position:absolute;right:142px;top:28px;display:flex;align-items:center;gap:18px;font-size:13px;font-weight:500;color:var(--ink);white-space:nowrap}
.main-nav .active{color:var(--red)}
.main-nav .quote{background:var(--navy);color:var(--white);padding:7px 8px}

/* hero */
.hero{left:0;top:0;width:1200px;height:547px;background:linear-gradient(100deg,#4f6b3a 0%,#6f8c4c 35%,#9aa88a 60%,#b9c0b0 100%)}
.hero-box{left:143px;top:268px;width:490px;height:146px;background:rgba(255,255,255,.72);padding:20px 18px}
.hero-title{font-family:"Open Sans",sans-serif;font-weight:700;font-size:26px;line-height:33px;color:#1f1f1f;text-transform:uppercase}

/* product circles */
.product{position:absolute;width:260px;text-align:center}
.product-circle{width:156px;height:156px;margin:0 auto;border-radius:50%;background:var(--white);border:10px solid rgba(255,255,255,.6);box-shadow:0 0 0 1px #e3e3e3;display:flex;align-items:center;justify-content:center}
.product-label{margin-top:22px;font-family:"Open Sans",sans-serif;font-weight:600;font-size:16px;color:var(--red);text-transform:uppercase;line-height:21px}

/* about */
.section-title{font-family:"Open Sans",sans-serif;font-size:26px;font-weight:600;letter-spacing:1px;text-transform:uppercase;color:var(--ink)}
.rule{position:absolute;height:1px;background:var(--line)}
.rule::before{content:"";position:absolute;left:0;top:-1px;height:4px;width:60px;background:var(--navy)}
.rule.center::before{left:50%;margin-left:-30px}
.body-text{font-size:13px;line-height:23px;color:var(--gray)}

.quote-card{left:820px;top:720px;width:238px;height:282px;background:#efefef;border:1px solid #ddd}
.quote-card h3{height:36px;background:var(--navy);color:var(--white);font-family:"Open Sans",sans-serif;font-weight:600;font-size:20px;text-align:center;line-height:36px}
.field{position:absolute;left:14px;width:210px;height:30px;border:1px solid #d3d3d3;background:#f7f7f7;font-size:11px;color:#888;padding:8px}

/* audience band */
.audience{top:1060px;width:600px;height:327px;text-align:center;color:var(--white)}
.audience h3{font-family:"Open Sans",sans-serif;font-weight:600;font-size:20px}
.audience p{font-size:13px;line-height:23px;width:340px;margin:10px auto 0}

/* insurance cards */
.policy{position:absolute;top:1544px;width:306px;height:413px}
.policy-body{position:absolute;left:0;bottom:0;width:100%;text-align:center;color:var(--white);padding:0 28px}
.policy-body h3{font-family:"Open Sans",sans-serif;font-weight:600;font-size:20px}
.policy-body .bar{width:40px;height:3px;background:var(--red);margin:12px auto 14px}
.policy-body p{font-size:11.5px;line-height:19px}

/* find agent */
.find-agent{left:0;top:2015px;width:1200px;height:291px;background:var(--navy-deep);text-align:center;color:var(--white)}
.search{left:440px;top:218px;width:156px;height:30px;background:var(--white);color:#888;font-size:12px;padding:8px 8px}

/* claim & contact */
.claim{left:160px;top:2360px;width:245px;text-align:center}
.claim .kicker{font-family:"Open Sans",sans-serif;font-size:25px;font-weight:600;color:var(--navy)}
.claim .big{font-family:"Open Sans",sans-serif;font-size:50px;font-weight:700;color:var(--red);line-height:62px}
.claim p{font-size:14px;line-height:26px;color:var(--navy);font-weight:500}
.input{position:absolute;height:32px;border:1px solid #d0d0d0;font-size:11px;color:#666;padding:9px}

/* footer */
.footer{left:0;top:2618px;width:1200px;height:250px;background:var(--footer);color:#cfcfcf}
.footer h4{font-family:"Raleway",sans-serif;font-weight:500;font-size:16px;color:var(--white)}
.footer .frule{height:1px;background:#444;margin-top:10px}
.quick-links li{list-style:none;font-size:11px;line-height:21.5px;color:#cfcfcf}
.quick-links li::before{content:"›";margin-right:6px;color:#888}
.quick-links li.current{color:#3e5aa3}
.copyright{left:0;top:2868px;width:1200px;height:35px;background:var(--navy)}
.social{width:20px;height:20px;background:#2f5fb5;border:1px solid #7fa0dd}
</style>
</head>
<body>

<!-- Hero -->
<div class="photo hero abs" role="img" aria-label="Family of three standing under a red umbrella on a leafy suburban street"></div>

<header class="site-header">
  <div class="brand"><span class="brand-mark"></span><span class="brand-name">HEARTHLINE<br>INSURANCE CO.</span></div>
  <nav class="main-nav">
    <span class="active">Home</span><span>About Us</span><span>Insurance</span><span>Agents</span><span>Claims</span><span>Contact Us</span><span class="quote">Get a quote</span>
  </nav>
</header>

<div class="hero-box abs">
  <h1 class="hero-title">Get homeowners insurance policy / tenants policy/ flood insurance in USA</h1>
</div>
<div class="btn btn-red" style="left:165px;top:398px;width:104px;height:30px">Read More</div>

<!-- Products -->
<div class="product" style="left:182px;top:470px">
  <div class="product-circle">
    <svg width="62" height="62" viewBox="0 0 62 62" fill="none" stroke="#d71f2c" stroke-width="3"><path d="M10 28 L31 10 L52 28"/><rect x="17" y="26" width="28" height="24" fill="#d71f2c" stroke="none"/><text x="31" y="44" text-anchor="middle" fill="#fff" stroke="none" font-family="Open Sans,sans-serif" font-size="14" font-weight="700">%</text><path d="M6 56 H56"/></svg>
  </div>
  <div class="product-label">Homeowners<br>Policy</div>
</div>
<div class="product" style="left:470px;top:470px">
  <div class="product-circle">
    <svg width="62" height="62" viewBox="0 0 62 62"><path d="M8 28 L31 8 L54 28 V52 H8 Z" fill="#d71f2c"/><circle cx="24" cy="30" r="4" fill="#fff"/><rect x="20" y="35" width="8" height="13" fill="#fff"/><circle cx="38" cy="30" r="4" fill="#fff"/><rect x="34" y="35" width="8" height="13" fill="#fff"/></svg>
  </div>
  <div class="product-label" style="margin-top:30px">Tenants Policy</div>
</div>
<div class="product" style="left:755px;top:470px">
  <div class="product-circle">
    <svg width="62" height="62" viewBox="0 0 62 62" fill="none" stroke="#d71f2c" stroke-width="3"><path d="M14 34 V20 L31 8 L48 20 V34 Z" fill="#d71f2c"/><path d="M6 42 q6 -5 12 0 t12 0 t12 0 t12 0"/><path d="M6 50 q6 -5 12 0 t12 0 t12 0 t12 0"/></svg>
  </div>
  <div class="product-label" style="margin-top:30px">Flood Insurance</div>
</div>

<!-- About -->
<h2 class="section-title abs" style="left:143px;top:730px">About Us</h2>
<div class="rule" style="left:143px;top:786px;width:615px"></div>
<p class="body-text abs" style="left:143px;top:806px;width:615px">Lorem ipsum dolor sit amet, consectetuer adipiscing elit, sed diam nonummy nibh euismod tincidunt ut laoreet dolore magna aliquam erat volutpat. Ut wisi enim ad minim veniam, quis nostrud exerci tation ullamcorper suscipit lobortis nisl ut aliquip ex ea commodo consequat. Duis autem vel eum iriure dolor in hendrerit in vulputate velit esse molestie consequat, vel illum dolore eu feugiat nulla facilisis at vero eros et accumsan et iusto odio dignissim qui blandit praesent luptatum zzril delenit augue duis dolore te feugait nulla facilisi.</p>
<div class="btn btn-navy" style="left:143px;top:970px;width:130px;height:30px">Read More</div>

<div class="quote-card abs">
  <h3>Get A Quote</h3>
  <div class="field" style="top:56px">Name</div>
  <div class="field" style="top:92px">Email</div>
  <div class="field" style="top:128px">Subject</div>
  <div class="field" style="top:164px;height:50px">Message</div>
  <div class="btn btn-navy" style="left:14px;top:228px;width:210px;height:30px">Submit</div>
</div>

<!-- Audience band -->
<div class="photo audience abs" style="left:0;background:linear-gradient(90deg,#1b1b1b,#3a3a3a 60%,#2a2a2a)" role="img" aria-label="Customers shaking hands with an insurance advisor at a desk">
  <svg style="margin-top:46px" width="60" height="44" viewBox="0 0 60 44" fill="#fff"><path d="M2 14 L14 8 L24 12 L32 8 L42 8 L58 16 L54 26 L44 34 L36 40 L30 36 L20 30 L10 26 Z"/><path d="M22 22 L30 18 L40 24" stroke="#1f1f1f" stroke-width="2" fill="none"/></svg>
  <h3 style="margin-top:10px">Customers</h3>
  <p>Lorem ipsum dolor sit amet, consectetuer adipiscing elit, sed diam nonummy nibh euismod tincidunt ut laoreet dolore magna aliquam erat volutpat</p>
</div>
<div class="btn btn-ghost" style="left:304px;top:1300px;width:128px;height:29px">Read More</div>

<div class="photo audience abs" style="left:600px;background:linear-gradient(90deg,#b5141f,#d71f2c 55%,#c41b27)" role="img" aria-label="Smiling insurance agent working at a laptop">
  <svg style="margin-top:36px" width="70" height="70" viewBox="0 0 70 70"><circle cx="35" cy="35" r="34" fill="#fff"/><circle cx="35" cy="24" r="7" fill="#d71f2c"/><path d="M24 46 q11 -18 22 0 Z" fill="#d71f2c"/><circle cx="20" cy="30" r="5" fill="#d71f2c"/><circle cx="50" cy="30" r="5" fill="#d71f2c"/><path d="M12 48 q8 -14 16 0 Z M42 48 q8 -14 16 0 Z" fill="#d71f2c"/></svg>
  <h3 style="margin-top:4px">Agents</h3>
  <p>Lorem ipsum dolor sit amet, consectetuer adipiscing elit, sed diam nonummy nibh euismod tincidunt ut laoreet dolore magna aliquam erat volutpat</p>
</div>
<div class="btn btn-ghost" style="left:764px;top:1300px;width:130px;height:29px">Read More</div>

<!-- Insurance -->
<div class="abs" style="left:0;top:1387px;width:1200px;height:628px;background:var(--light)"></div>
<h2 class="section-title abs" style="left:0;top:1432px;width:1200px;text-align:center">Insurance</h2>
<div class="rule center" style="left:292px;top:1490px;width:616px;background:#bbb"></div>

<div class="photo policy" style="left:141px;background:linear-gradient(180deg,#d8d8d8 0%,#8e8e8e 45%,#1c1c1c 80%)" role="img" aria-label="Couple looking around a bright new home interior">
  <div class="policy-body" style="bottom:82px"><h3>Homeowner Policy</h3><div class="bar"></div><p>Lorem ipsum dolor sit amet, consectetuer adipiscing elit, sed diam nonummy nibh euismod tincidunt ut laoreet dolore magna aliquam erat volutpat.</p></div>
</div>
<div class="photo policy" style="left:447px;background:linear-gradient(180deg,#e6d6c4 0%,#b09a86 40%,#1e3a7b 41%)" role="img" aria-label="Young couple reviewing a tenancy agreement together">
  <div class="policy-body" style="bottom:92px"><h3>Tenant Policy</h3><div class="bar"></div><p>Lorem ipsum dolor sit amet, consectetuer adipiscing elit, sed diam nonummy nibh euismod tincidunt ut laoreet dolore magna aliquam erat volutpat.</p></div>
</div>
<div class="photo policy" style="left:753px;width:305px;background:linear-gradient(180deg,#6f8d4e 0%,#8b4a3e 40%,#5b3a30 60%,#1c1c1c 80%)" role="img" aria-label="Red house tilted over after a flood">
  <div class="policy-body" style="bottom:82px"><h3>Flood Policy</h3><div class="bar"></div><p>Lorem ipsum dolor sit amet, consectetuer adipiscing elit, sed diam nonummy nibh euismod tincidunt ut laoreet dolore magna aliquam erat volutpat.</p></div>
</div>
<div class="btn btn-red" style="left:170px;top:1901px;width:108px;height:30px">Quote →</div>
<div class="btn btn-navy" style="left:287px;top:1901px;width:131px;height:30px">Read More →</div>
<div class="btn btn-red" style="left:476px;top:1890px;width:108px;height:30px">Quote →</div>
<div class="btn" style="left:593px;top:1890px;width:131px;height:30px;background:#fff;color:var(--red)">Read More →</div>
<div class="btn btn-red" style="left:782px;top:1901px;width:108px;height:30px">Quote →</div>
<div class="btn btn-navy" style="left:899px;top:1901px;width:131px;height:30px">Read More →</div>

<!-- Find an agent -->
<section class="find-agent abs">
  <h2 class="section-title" style="color:#fff;margin-top:47px">Find An Agent</h2>
  <div style="position:relative;margin:14px auto 0;width:616px;height:1px;background:#6c7ba4"><span style="position:absolute;left:278px;top:-1px;width:60px;height:4px;background:#fff"></span></div>
  <p class="body-text" style="color:#fff;width:620px;margin:30px auto 0">Lorem ipsum dolor sit amet, consectetuer adipiscing elit, sed diam nonummy nibh euismod tincidunt ut laoreet dolore magna aliquam erat volutpat. Ut wisi enim ad minim veniam, quis nostrud exerci tation ullamcorper suscipit lobortis nisl ut aliquip ex ea commodo consequat.</p>
  <div class="search abs" style="text-align:left">Search...</div>
  <div class="btn btn-red" style="left:604px;top:218px;width:157px;height:30px">Find An Agent</div>
</section>

<!-- Claims -->
<div class="claim abs">
  <div class="kicker">Report And Check</div>
  <div class="big">A Claim</div>
  <p>Login To Report A Claim Or<br>Check Your Claim Status.</p>
</div>
<div class="btn btn-red" style="left:238px;top:2531px;width:86px;height:30px">Login</div>
<div class="abs" style="left:436px;top:2335px;width:1px;height:250px;background:#ddd"></div>

<h2 class="abs head" style="left:485px;top:2355px;font-size:25px;font-weight:400;text-transform:uppercase">Contact Form</h2>
<div class="rule" style="left:485px;top:2402px;width:573px;background:#ccc"></div>
<div class="abs" style="left:485px;top:2415px;font-size:11px;color:#444">Please fill up bellow form</div>
<div class="input" style="left:485px;top:2438px;width:257px">Name</div>
<div class="input" style="left:753px;top:2438px;width:258px">Email</div>
<div class="input" style="left:485px;top:2484px;width:257px">Phone</div>
<div class="input" style="left:753px;top:2484px;width:258px">Message</div>
<div class="btn btn-red" style="left:485px;top:2531px;width:86px;height:30px">Submit</div>

<!-- Footer -->
<footer class="footer abs">
  <div class="abs" style="left:160px;top:45px;width:100px">
    <h4>Quick Links</h4><div class="frule"></div>
    <ul class="quick-links" style="margin-top:6px"><li class="current">Home</li><li>About Us</li><li>Insurance</li><li>Agents</li><li>Claims</li><li>Contact Us</li></ul>
  </div>
  <div class="abs" style="left:290px;top:45px;width:1px;height:180px;background:#333"></div>
  <div class="abs" style="left:338px;top:45px;width:185px">
    <h4>Contact Detail</h4><div class="frule"></div>
    <div style="margin-top:14px;font-size:12px;color:#fff;font-weight:600">Hearthline Insurance</div>
    <div style="font-size:11px;line-height:18px">Lorem ipsum dolor sit amet, consectetur adipiscing elit, sed do eiusmod</div>
    <div style="margin-top:24px;font-size:15px;display:flex;align-items:center;gap:10px"><svg width="13" height="13" viewBox="0 0 24 24" fill="#2f5fb5"><path d="M6 2 L10 2 L12 8 L9 10 Q11 15 14 15 L16 12 L22 14 L22 18 Q22 22 18 22 Q2 20 2 6 Q2 2 6 2Z"/></svg>555.014.2290</div>
    <div style="margin-top:14px;font-size:11px;display:flex;align-items:center;gap:10px"><svg width="13" height="10" viewBox="0 0 26 20" fill="#2f5fb5"><rect width="26" height="20"/><path d="M0 0 L13 11 L26 0" stroke="#1d1d1d" stroke-width="2" fill="none"/></svg>info@hearthline.com</div>
  </div>
  <div class="abs" style="left:574px;top:45px;width:1px;height:180px;background:#333"></div>
  <div class="abs" style="left:623px;top:45px;width:215px">
    <h4>Join Our Newsletter</h4><div class="frule"></div>
    <div style="margin-top:14px;font-size:11px;line-height:18px">Subscribe to our Newsletter to get the latest scoop right to your inbox</div>
    <div style="margin-top:10px;width:172px;height:30px;background:#444;color:#ddd;font-size:11px;padding:9px 8px">Enter Your Email</div>
    <div class="btn btn-red" style="position:relative;margin-top:12px;width:92px;height:28px;text-transform:none;font-weight:500">Subscribe</div>
  </div>
  <div class="abs" style="left:880px;top:60px;width:200px;height:120px;display:flex;align-items:center;justify-content:center;text-align:center;font-family:'Open Sans',sans-serif;font-weight:600;font-size:22px;line-height:28px;color:#bdbdbd">Hearthline<br>Insurance Co.</div>
</footer>
<div class="copyright abs">
  <div class="abs" style="left:143px;top:11px;font-size:11px;color:#fff;font-weight:600">© 2018 Hearthlineinsurance.com. All Rights Reserved.</div>
  <div class="abs" style="left:980px;top:7px;display:flex;gap:8px"><span class="social"></span><span class="social"></span><span class="social"></span></div>
</div>

</body>
</html>
```